Healthcare and Professional IT Services Company need a redesigned business card

We are a IT Services company that targets small medical practices and professional business such as Attorneys, Accounts, Architects etc. We want to communicate a professional yet friendly image using recent logo redesign here on ArtHarbor. Like to see the colors blue and orange in the design. Must use the Tall Pine Computing as displayed in the new logo - then also want to incorporate the fish logo as well.

Target Market(s)

Small medical and professional services

Industry/Entity Type

It Company

Contact Information for Business Card

The usual stuff, place for name address phone website. Also maybe our tagline which is "rooted in reliable tech"

Requirements
Must have
• My new logo and the fish somewhere on the card

```html
<!DOCTYPE html>
<html lang="en">
<head>
<meta charset="utf-8">
<title>Tall Pine Computing – Business Card</title>
<link rel="stylesheet" href="https://fonts.googleapis.com/css2?family=Open+Sans:wght@400;600;700&display=swap">
<style>
  :root {
    --stage: #242526;
    --blue: #0a95d8;
    --blue-deep: #0679b8;
    --blue-light: #2aa8e6;
    --orange: #f39121;
    --white: #ffffff;
    --paper-shade: #eef1f3;
    --ink-light: #e9f5fc;
    --ink-muted: #b9dcef;
  }
  * { box-sizing: border-box; margin: 0; padding: 0; }
  html, body {
    width: 1200px; height: 871px; overflow: hidden;
    background: var(--stage);
    font-family: "Open Sans", Arial, sans-serif;
  }
  .canvas {
    position: relative; width: 1200px; height: 871px;
    display: flex; flex-direction: column; align-items: center; justify-content: center; gap: 44px;
  }
  .card {
    position: relative; width: 640px; height: 366px; overflow: hidden;
    box-shadow: 0 14px 30px rgba(0,0,0,.45);
  }

  /* Back of card */
  .card--back {
    background: linear-gradient(135deg, var(--blue-light) 0%, var(--blue) 55%, var(--blue-deep) 100%);
    display: flex; flex-direction: column; align-items: center; justify-content: center; gap: 26px;
  }
  .back-brand { display: flex; align-items: center; gap: 14px; }
  .brand-dot {
    width: 30px; height: 30px; border-radius: 50%;
    background: var(--white); flex: none;
  }
  .back-brand .brand-name {
    font-size: 34px; font-weight: 600; color: var(--white); letter-spacing: .5px;
  }
  .tagline {
    font-size: 17px; font-weight: 600; color: var(--ink-light); letter-spacing: .4px;
  }

  /* Front of card */
  .card--front { background: var(--blue); }
  .front-top {
    position: absolute; left: 0; top: 0; width: 100%; height: 146px;
    background: linear-gradient(180deg, var(--white) 0%, var(--white) 70%, var(--paper-shade) 100%);
    display: flex; align-items: center; justify-content: center;
    border-bottom: 3px solid var(--orange);
  }
  .front-brand { display: flex; align-items: center; gap: 12px; }
  .front-brand .brand-dot { background: var(--blue); width: 26px; height: 26px; }
  .front-brand .brand-name {
    font-size: 36px; font-weight: 600; color: var(--blue); letter-spacing: .3px;
  }
  .front-bottom {
    position: absolute; left: 0; top: 149px; width: 100%; bottom: 0;
    background: linear-gradient(180deg, var(--blue) 0%, var(--blue-deep) 100%);
  }
  .contact {
    position: absolute; left: 38px; top: 30px;
    color: var(--white); font-size: 15px; line-height: 1.45;
  }
  .contact-address { margin-bottom: 8px; }
  .contact-list { list-style: none; }
  .contact-list li { display: flex; align-items: center; gap: 12px; }
  .contact-list svg { width: 15px; height: 15px; flex: none; }
  .person {
    position: absolute; right: 44px; bottom: 34px; text-align: right;
  }
  .person-name { font-size: 22px; font-weight: 700; color: var(--ink-muted); letter-spacing: .8px; }
  .person-title { font-size: 16px; color: var(--ink-muted); letter-spacing: .6px; }
</style>
</head>
<body>
<main class="canvas">

  <section class="card card--back" aria-label="Card back">
    <div class="back-brand">
      <span class="brand-dot"></span>
      <span class="brand-name">Tall Pine Computing</span>
    </div>
    <p class="tagline">rooted in reliable tech</p>
  </section>

  <section class="card card--front" aria-label="Card front">
    <header class="front-top">
      <div class="front-brand">
        <span class="brand-dot"></span>
        <span class="brand-name">Tall Pine Computing</span>
      </div>
    </header>
    <div class="front-bottom">
      <div class="contact">
        <p class="contact-address">4120 Harbor View Lane<br>Cedar Bay, OR 97001</p>
        <ul class="contact-list">
          <li>
            <svg viewBox="0 0 16 16" aria-hidden="true"><path fill="#fff" d="M2 6c0-2 2-3 6-3s6 1 6 3v1h-3V6H5v1H2zM4 8h8l1 5H3z"/></svg>
            555 0142 7781
          </li>
          <li>
            <svg viewBox="0 0 16 16" aria-hidden="true"><rect x="1.5" y="3.5" width="13" height="9" fill="#fff"/><path d="M1.5 3.5 8 9l6.5-5.5" fill="none" stroke="#0a95d8" stroke-width="1.3"/></svg>
            mara@tallpine.example
          </li>
          <li>
            <svg viewBox="0 0 16 16" aria-hidden="true"><circle cx="8" cy="8" r="6.5" fill="#fff"/><path d="M1.5 8h13M8 1.5c-3 3-3 10 0 13M8 1.5c3 3 3 10 0 13" fill="none" stroke="#0a95d8" stroke-width="1"/></svg>
            www.tallpine.example
          </li>
        </ul>
      </div>
      <div class="person">
        <p class="person-name">Mara Quill</p>
        <p class="person-title">President</p>
      </div>
    </div>
  </section>

</main>
</body>
</html>
```